Business card design for a dynamic IT consulting company

We need a business card design for a young firm, specialized in the Telecommunications/Consulting industry. The name of the company is Quindor and Partners Business Consulting Ltd. (Short name: Quindor and Partnes)
Quindor = solve read reverse, so we aim to be uncomplicated and solution-oriented. The small pipe in our logo is also related to the word solve. So we need a new business card design, which is simple, eye catching and something non traditional (I would probably prefer a square shaped design rather than a rectangle, but open for suggestions). Attached our logo.

Target Market(s)

Usually our customers are Tier1 Telecoms providers (Q-Netra, Palorix, etc) and their executives.

Industry/Entity Type

Business

Contact Information for Business Card

Name: Bence Tolnavari
Email: b.tolnavari@quindor.hu
Web: www.quindor.hu
Mobile: +36 30 518 2769
Title: Managing Director

Optional:
Company name: Quindor and Partners Ltd.
Address: 1087 Budapest, Tolvenka str. 28/C, Hungary

Font styles to use
Other font styles liked:
• helveticaneue_medium, Prime Regular are used now.

Colors

Designer to choose colors to be used in the design.

Requirements
Must have
• I would like to have a 2 sided design.
Nice to have
• I thought if we make the logo a bit bigger (without the company name), that could go to the back with the company name below. I though, if the pipe in the logo is somehow touchable on the business card, would be nice and unique.

```html
<!DOCTYPE html>
<html lang="en">
<head>
<meta charset="utf-8">
<title>Quindor and Partners – Business Card</title>
<link href="https://fonts.googleapis.com/css2?family=Arimo:wght@400;700&display=swap" rel="stylesheet">
<style>
  :root {
    --backdrop: #dcdcdc;
    --card: #f7f7f7;
    --accent-blue: #1a90d6;
    --text-grey: #555555;
    --brand-grey: #5f5f62;
    --brand-magenta: #b5338a;
  }
  html, body {
    margin: 0;
    padding: 0;
    width: 1200px;
    height: 960px;
    overflow: hidden;
    background: var(--backdrop);
    font-family: "Arimo", Helvetica, Arial, sans-serif;
  }
  .stage {
    position: relative;
    width: 1200px;
    height: 960px;
  }
  .card {
    position: absolute;
    top: 310px;
    width: 342px;
    height: 342px;
    background: var(--card);
    box-shadow: 1px 2px 4px rgba(0,0,0,0.35);
    text-align: center;
    color: var(--text-grey);
  }
  .card--front { left: 235px; }
  .card--back  { left: 623px; }

  .holder-name {
    position: absolute;
    top: 85px;
    left: 0;
    right: 0;
    margin: 0;
    font-size: 19px;
    font-weight: 700;
    color: var(--accent-blue);
    letter-spacing: 0.2px;
  }
  .holder-title {
    position: absolute;
    top: 108px;
    left: 0;
    right: 0;
    margin: 0;
    font-size: 15px;
    letter-spacing: 0.4px;
  }
  .company-address {
    position: absolute;
    top: 138px;
    left: 0;
    right: 0;
    margin: 0;
    font-size: 14px;
    line-height: 18px;
    font-style: normal;
  }
  .contact-list {
    position: absolute;
    top: 202px;
    left: 0;
    right: 0;
    margin: 0;
    padding: 0;
    list-style: none;
    font-size: 14px;
    line-height: 18px;
  }
  .contact-list li {
    display: flex;
    justify-content: center;
    align-items: center;
    gap: 2px;
  }
  .contact-icon {
    width: 12px;
    height: 12px;
    fill: var(--accent-blue);
  }

  .brand-lockup {
    position: absolute;
    top: 190px;
    left: 0;
    right: 0;
    display: flex;
    justify-content: center;
    align-items: center;
    gap: 8px;
  }
  .brand-name {
    font-size: 28px;
    font-weight: 400;
    color: var(--brand-grey);
    letter-spacing: 0.3px;
  }
  .brand-square {
    width: 9px;
    height: 9px;
    background: var(--brand-magenta);
  }
</style>
</head>
<body>
<main class="stage">
  <section class="card card--front">
    <h1 class="holder-name">BENCE TOLNAVARI</h1>
    <p class="holder-title">MANAGING DIRECTOR</p>
    <address class="company-address">
      Quindor and Partners Ltd.<br>
      1087 Budapest<br>
      Tolvenka str. 28/C, Hungary
    </address>
    <ul class="contact-list">
      <li>
        <svg class="contact-icon" viewBox="0 0 12 12" aria-hidden="true">
          <path d="M3 0h6a1 1 0 0 1 1 1v10a1 1 0 0 1-1 1H3a1 1 0 0 1-1-1V1a1 1 0 0 1 1-1zm0.6 1.5v7.8h4.8V1.5z"/>
        </svg>+36 30 518 2769
      </li>
      <li>
        <svg class="contact-icon" viewBox="0 0 12 12" aria-hidden="true">
          <path d="M0 2.5h12v7H0z M0.6 3l5.4 3.6L11.4 3" stroke="#f7f7f7" stroke-width="0.9"/>
        </svg>b.tolnavari@quindor.hu
      </li>
      <li>
        <svg class="contact-icon" viewBox="0 0 12 12" aria-hidden="true">
          <circle cx="6" cy="6" r="5.5"/>
          <path d="M0.5 6h11M6 0.5c-2.5 3-2.5 8 0 11M6 0.5c2.5 3 2.5 8 0 11" stroke="#f7f7f7" stroke-width="0.7" fill="none"/>
        </svg>www.quindor.hu
      </li>
    </ul>
  </section>

  <section class="card card--back">
    <div class="brand-lockup">
      <span class="brand-name">Quindor &amp; Partners</span>
      <span class="brand-square" aria-hidden="true"></span>
    </div>
  </section>
</main>
</body>
</html>
```